New Web Design Project open cart

We are about to start a new furniture selling website and it will be based on open cart . we mainly need two pages designing landing page & item page. so come up with your unique ideas and designs . Please make sure the design needs to be unique . no templates and themes . Will make the selected designer even happier if your design is selected. So basically over all it is going to be the new theme for our open cart base eCommerce website .we will appreciate if its responsive with some unique features .
SO as per request of designers about more brief about the project = WE ONLY NEED A RESPONSIVE THEME FOR OUR OPEN CART BASE eCommerce WebSite . Mainly item page & product page needs a good unique design. Lighter, speed load, compatible with all browsers and responsive will be appreciated . To Get an idea check on brindlework .co .uk website or timbrelhollow etc.
more projects coming soon .

Target Market(s)

Our audience will be furniture buying customers .

Industry/Entity Type

Furniture

Requirements
Must have
• to get some sort of idea have a look at brindlework .co uk`s website`s listing page and landing page .
Nice to have
• responsive, easy to customize, full theme .

```html
<!DOCTYPE html>
<html lang="en">
<head>
<meta charset="utf-8">
<title>Oakhaven – Furniture Store</title>
<link href="https://fonts.googleapis.com/css2?family=Open+Sans:wght@300;400;600;700&display=swap" rel="stylesheet">
<style>
  :root {
    --wood-light: #e9cf9c;
    --wood-mid: #dcb57a;
    --wood-dark: #c99a5c;
    --green: #8cc63e;
    --green-dark: #6fa52a;
    --orange: #f7941d;
    --red: #e5322d;
    --ink: #3a3a3a;
    --muted: #8a8a8a;
    --white: #ffffff;
    --shade: rgba(20, 20, 20, 0.55);
  }
  * { box-sizing: border-box; margin: 0; padding: 0; }
  html, body { width: 855px; height: 1200px; overflow: hidden; }
  body {
    font-family: "Open Sans", Arial, sans-serif;
    color: var(--ink);
    background: linear-gradient(90deg, var(--wood-light), var(--wood-mid) 30%, var(--wood-light) 55%, var(--wood-dark) 80%, var(--wood-light));
    position: relative;
  }
  .abs { position: absolute; }

  /* header */
  .brand { left: 84px; top: 14px; display: flex; align-items: center; gap: 8px; }
  .brand-mark { width: 26px; height: 26px; background: var(--orange); }
  .brand-name { font-size: 28px; font-weight: 700; color: var(--ink); }
  .top-links { left: 560px; top: 8px; display: flex; gap: 18px; font-size: 8px; color: var(--ink); }
  .phone { left: 592px; top: 62px; font-size: 9px; display: flex; align-items: center; gap: 5px; }
  .cart { left: 690px; top: 42px; width: 82px; height: 62px; background: var(--orange); color: var(--white); padding: 10px 10px 0 32px; font-size: 11px; font-weight: 600; }
  .cart svg { position: absolute; left: 9px; top: 12px; }
  .cart small { display: block; font-size: 7px; font-weight: 400; margin-top: 10px; }

  .main-nav { left: 80px; top: 112px; width: 695px; height: 28px; background: var(--green); display: flex; justify-content: space-between; padding: 0 26px; align-items: center; font-size: 9px; font-weight: 600; color: var(--white); }

  /* hero */
  .photo { background: linear-gradient(135deg, #6b5033, #b89366 45%, #e4d0ad 70%, #7a5c3c); }
  .photo.dark { background: linear-gradient(135deg, #2c2a28, #5b554d 50%, #8a7f70); }
  .photo.pale { background: linear-gradient(135deg, #d9d4cc, #f2efe9 50%, #b7ada0); }
  .hero-main { left: 80px; top: 142px; width: 432px; height: 282px; }
  .hero-caption { left: 80px; top: 365px; width: 432px; height: 40px; background: var(--shade); color: var(--white); font-size: 17px; padding: 7px 0 0 30px; }
  .hero-caption::before { content: ""; position: absolute; left: 0; top: 0; width: 16px; height: 40px; background: var(--green); }
  .hero-tile { width: 144px; height: 224px; top: 426px; }
  .tile-caption { position: absolute; left: 0; right: 0; top: 62px; text-align: center; color: var(--white); font-size: 11px; font-weight: 700; line-height: 1.3; padding: 0 14px; }
  .side-tile { left: 514px; width: 261px; }
  .side-label { position: absolute; left: 58px; bottom: 14px; background: rgba(255,255,255,0.18); color: var(--white); font-size: 26px; font-weight: 300; line-height: 1; padding: 6px 10px; }
  .side-label b { display: block; color: var(--green); font-weight: 600; }

  /* intro */
  .intro { left: 80px; top: 650px; width: 695px; height: 145px; background: var(--white); text-align: center; padding: 28px 40px 0; }
  .intro h1 { font-size: 21px; font-weight: 300; color: var(--orange); margin-bottom: 10px; }
  .intro p { font-size: 7.5px; line-height: 1.55; color: var(--muted); }
  .btn-more { display: inline-block; margin-top: 10px; background: var(--red); color: var(--white); font-size: 9px; font-weight: 600; padding: 4px 22px; }

  /* products */
  .products { left: 80px; top: 812px; width: 695px; display: flex; gap: 17px; }
  .card { width: 161px; height: 240px; background: var(--white); padding: 6px; }
  .card-img { height: 128px; }
  .price { color: var(--orange); font-size: 11px; font-weight: 700; margin-top: 8px; }
  .name { font-size: 9px; font-weight: 600; margin-top: 2px; }
  .desc { font-size: 7px; color: var(--muted); line-height: 1.45; margin-top: 4px; }
  .actions { display: flex; gap: 3px; margin-top: 10px; }
  .add { background: var(--orange); width: 64px; height: 16px; }
  .mini { width: 16px; height: 16px; background: #eee; display: flex; align-items: center; justify-content: center; font-size: 8px; color: var(--muted); }

  /* footer */
  .footer { left: 80px; top: 1078px; width: 695px; display: flex; justify-content: space-between; }
  .footer-col { width: 150px; }
  .footer-col h3 { font-size: 10px; font-weight: 600; border-bottom: 1px solid rgba(0,0,0,0.15); padding-bottom: 4px; margin-bottom: 6px; }
  .footer-col li { list-style: none; font-size: 7px; line-height: 1.75; padding-left: 8px; position: relative; }
  .footer-col li::before { content: ""; position: absolute; left: 0; top: 5px; width: 3px; height: 3px; background: var(--ink); border-radius: 50%; }
  .social { display: flex; gap: 5px; margin-top: 4px; }
  .social span { width: 13px; height: 13px; border-radius: 50%; }
  .legal { left: 84px; top: 1172px; display: flex; align-items: center; gap: 8px; font-size: 7px; }
  .legal .dot { width: 12px; height: 12px; background: var(--orange); }
  .legal strong { font-size: 11px; }
</style>
</head>
<body>

<header>
  <div class="abs brand"><span class="brand-mark"></span><span class="brand-name">Oakhaven</span></div>
  <nav class="abs top-links"><span>Home</span><span>Wish List</span><span>My Account</span><span>Shopping Cart</span><span>Checkout</span></nav>
  <div class="abs phone">
    <svg width="9" height="9" viewBox="0 0 24 24"><path fill="#3a3a3a" d="M6.6 10.8a15 15 0 006.6 6.6l2.2-2.2c.3-.3.7-.4 1-.2 1.1.4 2.3.6 3.6.6.6 0 1 .4 1 1V20c0 .6-.4 1-1 1A17 17 0 013 4c0-.6.4-1 1-1h3.5c.6 0 1 .4 1 1 0 1.3.2 2.5.6 3.6.1.3 0 .7-.2 1z"/></svg>
    0800-5550 172
  </div>
  <div class="abs cart">
    <svg width="18" height="16" viewBox="0 0 24 22"><path fill="none" stroke="#fff" stroke-width="2" d="M1 2h4l3 12h12l3-9H7"/><circle cx="10" cy="19" r="2" fill="#fff"/><circle cx="18" cy="19" r="2" fill="#fff"/></svg>
    Cart<small>0 items – $0.00</small>
  </div>
  <nav class="abs main-nav"><span>Living Room</span><span>Dining Room</span><span>Bedroom</span><span>Accent Chairs</span><span>Accessories</span><span>Kids' World</span><span>Office</span></nav>
</header>

<section class="hero">
  <div class="abs hero-main photo" role="img" aria-label="Ornate carved bed with cream upholstery in a classic bedroom"></div>
  <div class="abs hero-caption">Phasellus blandit velit at fgilla andit velit</div>

  <div class="abs hero-tile photo dark" style="left:80px" role="img" aria-label="Dark interior with an accent lamp"><div class="tile-caption">Phasellus blandit velit at fgilla</div></div>
  <div class="abs hero-tile photo dark" style="left:225px" role="img" aria-label="Living room with a sofa and side table"><div class="tile-caption">Phasellus blandit velit at fgilla</div></div>
  <div class="abs hero-tile photo dark" style="left:370px;width:142px" role="img" aria-label="Bedroom with a classic bed frame"><div class="tile-caption">Phasellus blandit velit at fgilla</div></div>

  <div class="abs side-tile photo dark" style="top:142px;height:148px" role="img" aria-label="Modern sofa in a living room"><div class="side-label">Modern<b>Sofas</b></div></div>
  <div class="abs side-tile photo" style="top:292px;height:156px" role="img" aria-label="Modern upholstered chair"><div class="side-label">Modern<b>Chair</b></div></div>
  <div class="abs side-tile photo pale" style="top:450px;height:200px" role="img" aria-label="Canopy bed with white drapes"><div class="side-label">Modern<b>Sofas</b></div></div>
</section>

<section class="abs intro">
  <h1>Creative Design &amp; Quality Construction</h1>
  <p>Our pieces are shaped by skilled hands from solid timber and chosen fabrics, built to last for years of daily family use. Each sofa, table and bed frame is checked at every stage before it leaves the workshop. We offer free delivery on larger orders, simple returns and friendly advice from our team whenever you need help choosing the right piece for your home.</p>
  <span class="btn-more">More</span>
</section>

<section class="abs products">
  <article class="card"><div class="card-img photo" role="img" aria-label="Carved upholstered armchair"></div><div class="price">$119.00</div><div class="name">Incididunt ut</div><p class="desc">Solid wood finish with soft fabric seat.</p><div class="actions"><span class="add"></span><span class="mini">♥</span><span class="mini">⇄</span></div></article>
  <article class="card"><div class="card-img photo pale" role="img" aria-label="Round dark wood pedestal table"></div><div class="price">$119.00</div><div class="name">Incididunt ut</div><p class="desc">Solid wood finish with soft fabric seat.</p><div class="actions"><span class="add"></span><span class="mini">♥</span><span class="mini">⇄</span></div></article>
  <article class="card"><div class="card-img photo" role="img" aria-label="Classic side chair with curved legs"></div><div class="price">$119.00</div><div class="name">Incididunt ut</div><p class="desc">Solid wood finish with soft fabric seat.</p><div class="actions"><span class="add"></span><span class="mini">♥</span><span class="mini">⇄</span></div></article>
  <article class="card"><div class="card-img photo" role="img" aria-label="Tall wooden wardrobe"></div><div class="price">$119.00</div><div class="name">Incididunt ut</div><p class="desc">Solid wood finish with soft fabric seat.</p><div class="actions"><span class="add"></span><span class="mini">♥</span><span class="mini">⇄</span></div></article>
</section>

<footer>
  <div class="abs footer">
    <div class="footer-col"><h3>Information</h3><ul><li>About Us</li><li>Delivery Information</li><li>Privacy Policy</li><li>Terms &amp; Conditions</li></ul></div>
    <div class="footer-col"><h3>Customer Service</h3><ul><li>Contact Us</li><li>Returns</li><li>Site Map</li></ul></div>
    <div class="footer-col"><h3>Extras</h3><ul><li>Brands</li><li>Gift Vouchers</li><li>Affiliates</li><li>Specials</li></ul></div>
    <div class="footer-col"><h3>My Account</h3><ul><li>My Account</li><li>Order History</li><li>Wish List</li><li>Newsletter</li></ul>
      <div class="social"><span style="background:#3b5998"></span><span style="background:#33ccff"></span><span style="background:#e5322d"></span><span style="background:#f7941d"></span></div>
    </div>
  </div>
  <div class="abs legal"><span class="dot"></span><strong>Oakhaven</strong><span>© 2014 Privacy policy</span></div>
</footer>

</body>
</html>
```